Business Cards for IT Consulting Company (Managed Service Provider)

I am looking to have some business cards printed and would like some designs. We are an IT Consulting company based in Vancouver BC. I would like a nice clean and modern look to the cards. I have uploaded all the versions of my logo so parts can be used as needed. Here is a snippit from our website homepage:

Quillbrook Networks Ltd. is an IT Solutions Partner located in Vancouver BC, Canada. We offer IT solutions and support to customers in the greater Vancouver Area. With expertise in Microsoft platforms, as well as Linux and Mac OSX and over 12 years experience in the IT industry, Quillbrook Networks is dedicated to offering our clients top quality service and products. We take pride in the solutions we offer our customers. The greatest compliment a client can give us is to recommend our services.

Quillbrook Networks Ltd. offers a wide range of IT services from onsite service to remote support and managed service solutions. This allows clients to choose the support path that best suits their company’s needs. Supporting many different sized companies from small to enterprise level over the past 12 years Quillbrook Networks has the experience and expertise needed to ensure things run smoothly. Allowing our clients to focus on doing business.

Revolutionizing the way IT services are delivered.

Quillbrook Networks is dedicated to providing our clients with IT solutions that work and grow with them for years to come. This philosophy helps save money in the long run instead of replacing equipment constantly. Far too often IT solutions are not well thought out and while possibly solving the problem at hand, require replacement due to growth or quality within a very short time frame. Quillbrook Networks takes pride in providing solutions that will last and be able to accommodate growth without the need for replacement.

Industry/Entity Type

Information Technology

Contact Information for Business Card

Quillbrook Networks Ltd.
(Employee Name)
Eml: (Employees Email Address)
Web: quillbrook.me
Ph: 604-555-0148

Font styles to use
Serif
Sans Serif

Requirements
Must have
• The Company logo and company colors.
Nice to have
• - Our tag line: "Revolutionizing IT Services" or "Revolutionizing the way IT services are delivered."
• - Also I really like the idea of nature and technology together blending which is sort of where my logo came from so integrating that somehow onto the business cards would be great.

```html
<!DOCTYPE html>
<html lang="en">
<head>
<meta charset="utf-8">
<title>Quillbrook Networks Ltd. — Business Card</title>
<link rel="stylesheet" href="https://fonts.googleapis.com/css2?family=Montserrat:wght@400;500;600;700&display=swap">
<style>
  :root {
    --brand-blue: #1fa9e6;
    --band-grey: #5f6062;
    --ink-grey: #5a5a5c;
    --card-white: #ffffff;
    --backdrop: #e6e7e9;
  }
  * { box-sizing: border-box; margin: 0; padding: 0; }
  html, body {
    width: 1200px; height: 900px; overflow: hidden;
    background: var(--backdrop);
    font-family: "Montserrat", Arial, sans-serif;
  }
  .stage { position: relative; width: 1200px; height: 900px; }
  .card {
    position: absolute; left: 250px; width: 700px; height: 400px;
    background: var(--card-white); overflow: hidden;
    box-shadow: 0 6px 18px rgba(0,0,0,.18);
  }
  .card--front-face { top: 35px; }
  .card--contact { top: 465px; }

  /* Shared wordmark */
  .wordmark {
    position: absolute; display: flex; align-items: center; gap: 12px;
    color: var(--brand-blue); font-weight: 600; white-space: nowrap; line-height: 1;
  }
  .wordmark__square { display: block; flex: none; border: 3px solid var(--brand-blue); }

  /* Tagline side */
  .card--front-face .wordmark { right: 50px; top: 80px; font-size: 26px; }
  .card--front-face .wordmark__square { width: 40px; height: 40px; }
  .tagline {
    position: absolute; left: 150px; top: 230px;
    font-size: 17px; font-weight: 500; letter-spacing: 1.2px; color: var(--ink-grey);
  }

  /* Contact side */
  .band { position: absolute; inset: 0; width: 700px; height: 400px; }
  .band path { fill: var(--band-grey); }
  .card--contact .wordmark { left: 60px; top: 80px; font-size: 30px; }
  .card--contact .wordmark__square { width: 46px; height: 46px; }

  .person { position: absolute; left: 60px; top: 264px; color: var(--card-white); }
  .person__name {
    font-size: 22px; font-weight: 700; letter-spacing: 2px; color: var(--brand-blue);
    text-transform: uppercase; line-height: 1.1;
  }
  .person__role { font-size: 14px; font-weight: 500; letter-spacing: 1px; margin-top: 4px; }
  .contact-list { list-style: none; margin-top: 10px; }
  .contact-list li {
    display: flex; align-items: center; gap: 10px;
    font-size: 15px; font-weight: 500; letter-spacing: .8px; line-height: 22px;
  }
  .contact-list svg { width: 12px; height: 12px; flex: none; }
  .contact-list svg * { fill: none; stroke: var(--brand-blue); stroke-width: 2; }
  .contact-list .icon-fill { fill: var(--brand-blue); stroke: none; }
</style>
</head>
<body>
<main class="stage">

  <section class="card card--front-face" aria-label="Card front">
    <div class="wordmark"><span class="wordmark__square"></span>Quillbrook Networks</div>
    <p class="tagline">Revolutionizing IT Services</p>
  </section>

  <section class="card card--contact" aria-label="Card back">
    <svg class="band" viewBox="0 0 700 400" aria-hidden="true">
      <path d="M0 255 H400 V150 H700 V400 H0 Z"/>
    </svg>
    <div class="wordmark"><span class="wordmark__square"></span>Quillbrook Networks Ltd.</div>
    <div class="person">
      <p class="person__name">Maren Holt</p>
      <p class="person__role">DIRECTOR</p>
      <ul class="contact-list">
        <li>
          <svg viewBox="0 0 12 12" aria-hidden="true"><path class="icon-fill" d="M2 1h3l1 3-2 1c1 2 2 3 3 3l1-2 3 1v3c-6 0-10-4-9-9z"/></svg>
          604-555-0148
        </li>
        <li>
          <svg viewBox="0 0 12 12" aria-hidden="true"><rect x="1" y="2.5" width="10" height="7"/><path d="M1 2.5l5 4 5-4"/></svg>
          info@marenholt.com
        </li>
        <li>
          <svg viewBox="0 0 12 12" aria-hidden="true"><circle cx="6" cy="6" r="5"/><path d="M1 6h10M6 1c-3 3-3 7 0 10M6 1c3 3 3 7 0 10"/></svg>
          www.quillbrook.me
        </li>
      </ul>
    </div>
  </section>

</main>
</body>
</html>
```